Design a label for a dog shampoo names fluffo, the sell point of this series of shampoo is “just like wash your dogs with milk, not harm for your hand ”, the style could be gentle or professional or even amazing.

Use only 2 colors in the design job, the color of our logo could be changed, it depends on your whole page. Please design in CDR or ai.

update:
Pls do more change with the fonts when you design the front page, including title and details. Try more styles of fonts. Addition, this design will be printed on the bottle, no a label stick on it.
Updates

Do not put a real dog or animal on the page, Pay more attention to the types of fonts

Reason: Expect for more design idea.

Target Market(s)

people 20-30 years old who have dogs and cats at home

Industry/Entity Type

It Professional

Requirements
Nice to have
• It would be nice if you add some detail words in the design of the right side.

```html
<!DOCTYPE html>
<html lang="en">
<head>
<meta charset="utf-8">
<title>fluffo shampoo bottle print – three colour options</title>
<link rel="stylesheet" href="https://fonts.googleapis.com/css2?family=Baloo+2:wght@700;800&family=Chewy&family=Codystar&family=Oswald:wght@600&family=Roboto+Condensed:ital,wght@0,800;1,800&display=swap">
<style>
  :root {
    --teal: #0fb0cc;
    --sky: #29a8e0;
    --blue: #1b7fc4;
    --orange: #f7941d;
    --magenta: #ec008c;
    --ink: #111111;
    --white: #ffffff;
    --foam: #d7eef7;
    --frame: #c8c8c8;
  }
  * { box-sizing: border-box; margin: 0; padding: 0; }
  html, body { width: 1200px; height: 767px; overflow: hidden; background: var(--white); }
  .sheet { position: relative; width: 1200px; height: 767px; }
  .panel { position: absolute; top: 0; height: 767px; overflow: hidden; background: var(--white); }
  .panel--bubbly { left: 0; width: 401px; }
  .panel--orange { left: 401px; width: 400px; }
  .panel--magenta { left: 802px; width: 398px; border: 1px solid var(--frame); }

  .foam {
    position: absolute; left: 0; right: 0; top: 380px; bottom: 0;
    background: linear-gradient(180deg, rgba(215,238,247,0) 0%, rgba(215,238,247,0.6) 35%, var(--foam) 70%, #c2e5f3 100%);
  }
  .paws {
    position: absolute; left: 30px; right: 30px; top: 515px; height: 170px;
    border-radius: 50%;
    background: radial-gradient(ellipse at 50% 50%, rgba(26,26,26,0.85) 0%, rgba(26,26,26,0.55) 45%, rgba(215,238,247,0) 72%);
  }

  .badge { position: absolute; left: 50%; top: 20px; transform: translateX(-50%); width: 200px; height: 116px; }
  .badge__name {
    position: absolute; inset: 0; display: flex; align-items: center; justify-content: center;
    font-family: "Baloo 2", sans-serif; font-weight: 700; font-size: 38px; color: var(--white);
  }

  .line { position: absolute; left: 0; right: 0; text-align: center; white-space: nowrap; }

  /* bubbly option */
  .bubbly-tag { top: 202px; font-family: "Chewy", "Baloo 2", cursive; font-size: 17px; color: var(--white);
    -webkit-text-stroke: 1px var(--sky); letter-spacing: 0.5px; }
  .bubbly-title { top: 222px; font-family: "Chewy", "Baloo 2", cursive; font-size: 88px; line-height: 1; color: var(--white);
    -webkit-text-stroke: 3px var(--blue); text-shadow: 3px 3px 0 var(--blue); letter-spacing: 2px; }
  .bubbly-claim { top: 320px; font-family: "Chewy", "Baloo 2", cursive; font-size: 19px; line-height: 22px; color: var(--white);
    -webkit-text-stroke: 1px var(--ink); letter-spacing: 0.5px; }
  .bubbly-benefit { top: 405px; font-family: "Codystar", cursive; font-size: 28px; line-height: 37px;
    color: var(--blue); -webkit-text-stroke: 1.2px var(--blue); letter-spacing: 2px; }
  .bubbly-volume { top: 712px; font-family: "Roboto Condensed", sans-serif; font-weight: 800; font-style: italic;
    font-size: 18px; color: var(--ink); }

  /* condensed options */
  .cond-tag { top: 189px; font-family: "Oswald", sans-serif; font-weight: 600; font-size: 19px; letter-spacing: 0.3px; }
  .cond-title { top: 208px; font-family: "Oswald", sans-serif; font-weight: 600; font-size: 80px; line-height: 1.1; letter-spacing: 1px; }
  .cond-benefit { top: 308px; font-family: "Roboto Condensed", sans-serif; font-weight: 800; font-size: 20px; line-height: 26px; letter-spacing: 0.5px; }
  .cond-claim { top: 455px; font-family: "Baloo 2", sans-serif; font-weight: 700; font-size: 19px; line-height: 22px; }
  .cond-volume { top: 704px; font-family: "Roboto Condensed", sans-serif; font-weight: 800; font-size: 19px; }

  .panel--orange .cond-tag { color: var(--sky); }
  .panel--orange .cond-title { color: var(--orange); }
  .panel--orange .cond-benefit { color: var(--sky); }
  .panel--orange .cond-claim { color: var(--orange); transform: rotate(-6deg); top: 462px; }
  .panel--orange .cond-volume { color: var(--orange); }

  .panel--magenta .cond-tag { color: var(--ink); }
  .panel--magenta .cond-title { color: var(--magenta); }
  .panel--magenta .cond-benefit { color: var(--ink); }
  .panel--magenta .cond-claim { color: var(--magenta); }
  .panel--magenta .cond-volume { color: var(--ink); }
</style>
</head>
<body>
<main class="sheet">

  <section class="panel panel--bubbly">
    <div class="foam" role="img" aria-label="Soap bubbles rising from the bottom"></div>
    <div class="paws" role="img" aria-label="Two black paw prints among the bubbles"></div>
    <div class="badge">
      <svg width="200" height="116" viewBox="0 0 200 116" aria-hidden="true">
        <ellipse cx="100" cy="58" rx="98" ry="56" fill="var(--teal)"/>
        <ellipse cx="100" cy="58" rx="91" ry="50" fill="none" stroke="var(--white)" stroke-width="1.2" stroke-dasharray="2 3"/>
      </svg>
      <span class="badge__name">fluffo</span>
    </div>
    <p class="line bubbly-tag">super-conditioning &amp; nutrient</p>
    <h1 class="line bubbly-title">Shampoo</h1>
    <p class="line bubbly-claim">wash your dogs just like with milk<br>not harm for your hand</p>
    <p class="line bubbly-benefit">MOISTURE-RICH<br>SMOOTH AND<br>SILKY</p>
    <p class="line bubbly-volume">1000 ML</p>
  </section>

  <section class="panel panel--orange">
    <div class="foam" role="img" aria-label="Soap bubbles rising from the bottom"></div>
    <div class="paws" role="img" aria-label="Two black paw prints among the bubbles"></div>
    <div class="badge">
      <svg width="200" height="116" viewBox="0 0 200 116" aria-hidden="true">
        <ellipse cx="100" cy="58" rx="98" ry="56" fill="var(--teal)"/>
        <ellipse cx="100" cy="58" rx="91" ry="50" fill="none" stroke="var(--white)" stroke-width="1.2" stroke-dasharray="2 3"/>
      </svg>
      <span class="badge__name">fluffo</span>
    </div>
    <p class="line cond-tag">SUPER-CONDITIONING &amp; NUTRIENT</p>
    <h1 class="line cond-title">SHAMPOO</h1>
    <p class="line cond-benefit">MOISTURE-RICH, SMOOTH<br>AND SILKY</p>
    <p class="line cond-claim">wash your dogs just like with milk<br>not harm for your hand</p>
    <p class="line cond-volume">1000 ML</p>
  </section>

  <section class="panel panel--magenta">
    <div class="foam" role="img" aria-label="Soap bubbles rising from the bottom"></div>
    <div class="paws" role="img" aria-label="Two black paw prints among the bubbles"></div>
    <div class="badge">
      <svg width="200" height="116" viewBox="0 0 200 116" aria-hidden="true">
        <ellipse cx="100" cy="58" rx="98" ry="56" fill="var(--teal)"/>
        <ellipse cx="100" cy="58" rx="91" ry="50" fill="none" stroke="var(--white)" stroke-width="1.2" stroke-dasharray="2 3"/>
      </svg>
      <span class="badge__name">fluffo</span>
    </div>
    <p class="line cond-tag">SUPER-CONDITIONING &amp; NUTRIENT</p>
    <h1 class="line cond-title">SHAMPOO</h1>
    <p class="line cond-benefit">MOISTURE-RICH, SMOOTH<br>AND SILKY</p>
    <p class="line cond-claim">wash your dogs just like with milk<br>not harm for your hand</p>
    <p class="line cond-volume">1000 ML</p>
  </section>

</main>
</body>
</html>
```